Reginald's Book Cover

Need a cover design for a book (paperback and eBook)
Book Title: Songs From The Old Trapline
Book Width: 15.24
Book Height: 22.86
Thickness: approximately 200 pages.
Book is a collection of stories drawn from the author's life, and will be in the local history genre in northern British Columbia, Canada from the period 1930 to the present time.
Author: Reginald Hugh Pettigrew
Must include "As told to Wendy Falkner" on front cover, not on the spine.
Author invites designers creativity and asks that the attached photos be incorporated into the front and back covers in tasteful ways as follows:
- Back Cover_Reginald_Marta_Knobby – goes on back cover
- Back Cover_Grizzly - goes on the back cover
- Front Cover_Mountain Flowers - goes on the front cover
- Front Cover_Reginald_in Alpine - goes on the front cover
Other uses of the photos will be considered.
We apologize for the quality of the photos. Please do what you can.
We look forward to your designs.
Thank you for considering.

Target Market(s)

Lovers of local history, jokes, storytelling, back country hiking and mountain climbing. Men and women 30 years and older. Primary target readership are men and women in their 40's, 50's, 60's, and older, who love local history

Font styles to use
Sans Serif

Requirements
Must have
• Back cover copy must clear and easy to read.
Must appeal to outdoor, back country types.
Nice to have
• Like to see a creative incorporation of the photos provided.
Build on or compliment the colours in the photos

```html
<!DOCTYPE html>
<html lang="en">
<head>
<meta charset="utf-8">
<title>Songs From The Old Trapline – Cover Wrap</title>
<link rel="stylesheet" href="https://fonts.googleapis.com/css2?family=Anton&family=Arimo:wght@400&display=swap">
<style>
  :root {
    --white: #ffffff;
    --ink-panel: rgba(38, 36, 34, 0.78);
    --author-band: rgba(40, 40, 40, 0.85);
    --sky-dark: #3d4046;
    --sky-mid: #6b6d68;
    --meadow-dark: #3e3f22;
    --meadow-mid: #6d6a33;
    --meadow-bright: #8e8a3f;
    --alpine-green: #4f8a35;
    --alpine-light: #7fb04a;
    --alpine-deep: #2f5a26;
    --spine-green: #35652b;
  }
  * { margin: 0; padding: 0; box-sizing: border-box; }
  html, body { width: 1200px; height: 831px; overflow: hidden; background: #222; }
  .cover-wrap { position: relative; width: 1200px; height: 831px; overflow: hidden; font-family: "Arimo", Arial, sans-serif; color: var(--white); }

  /* Back cover */
  .back-cover { position: absolute; left: 0; top: 0; width: 554px; height: 831px; }
  .back-photo {
    position: absolute; inset: 0;
    background: linear-gradient(180deg, var(--sky-dark) 0%, var(--sky-mid) 28%, var(--meadow-mid) 42%, var(--meadow-bright) 60%, var(--meadow-dark) 100%);
  }
  .back-copy-panel { position: absolute; left: 163px; top: 0; width: 391px; height: 831px; background: var(--ink-panel); }
  .back-copy {
    position: absolute; left: 219px; top: 57px; width: 279px;
    font-size: 17px; line-height: 19.2px; text-align: justify; color: var(--white);
  }
  .back-copy p + p { margin-top: 19px; }

  /* Spine */
  .spine { position: absolute; left: 554px; top: 0; width: 92px; height: 831px;
    background: linear-gradient(180deg, var(--alpine-light) 0%, var(--spine-green) 40%, var(--alpine-deep) 100%); }
  .spine-photo { position: absolute; left: 0; top: 52px; width: 70px; height: 156px;
    background: linear-gradient(180deg, #5f8c44 0%, #7a9a5a 50%, #4d7a38 100%); }
  .spine-title {
    position: absolute; left: 24px; top: 278px; height: 520px;
    writing-mode: vertical-rl;
    font-family: "Anton", "Arial Narrow", sans-serif; font-size: 40px; line-height: 44px;
    letter-spacing: 0.2px; text-transform: uppercase; white-space: nowrap;
  }

  /* Front cover */
  .front-cover { position: absolute; left: 646px; top: 0; width: 554px; height: 831px; }
  .front-photo { position: absolute; inset: 0;
    background:
      radial-gradient(ellipse at 50% 75%, rgba(60, 80, 140, 0.25), transparent 45%),
      linear-gradient(180deg, #607a58 0%, var(--alpine-green) 22%, var(--alpine-light) 45%, var(--alpine-green) 70%, #5f8a2c 100%); }

  .title-block { position: absolute; right: 29px; top: 66px; text-align: right;
    font-family: "Anton", "Arial Narrow", sans-serif; font-weight: 400; text-transform: uppercase; color: var(--white); }
  .title-line { display: block; white-space: nowrap; }
  .title-line--lead { font-size: 76px; line-height: 80px; }
  .title-line--lead .title-small { font-size: 46px; }
  .title-line--hero { font-size: 146px; line-height: 146px; letter-spacing: -1px; }

  .photo-insets { position: absolute; left: 319px; top: 316px; width: 222px; height: 316px; }

  .author-band { position: absolute; left: 228px; top: 731px; width: 326px; height: 83px; }
  .author-band svg { position: absolute; inset: 0; }
  .author-name { position: absolute; right: 32px; top: 14px; font-size: 19.5px; line-height: 24px; white-space: nowrap; }
  .author-rule { position: absolute; left: 57px; right: 32px; top: 45px; height: 1px; background: rgba(255,255,255,0.7); }
  .author-credit { position: absolute; right: 32px; top: 54px; font-size: 16px; line-height: 20px; white-space: nowrap; }
</style>
</head>
<body>
<div class="cover-wrap">

  <section class="back-cover">
    <div class="back-photo" role="img" aria-label="Alpine meadow of wildflowers under a stormy sky with distant snowy peaks"></div>
    <div class="back-copy-panel"></div>
    <div class="back-copy">
      <p>Reginald Pettigrew is a true old-fashioned story teller. He loves nothing better than a good story, and particularly when he is the one telling the story. He was born and raised in the tiny sawmill town of Penny, BC and spent 80 years of his life there before relocating to his current home on the banks of the Nechako River in Prince George, BC. In addition to writing this book, Reginald spends his time writing songs, singing, telling jokes, and entertaining his many friends with stories of days gone by.</p>
      <p>At the age of 15 he started his career as a flunky in the cookhouse, then moved on to work as a horse logger, sawmill worker, bush foreman, rancher, cat skinner, forest warden, road and bridge builder, and finished his career as salmon hatchery manager.</p>
      <p>Reginald’s love of the mountains is evident throughout the book, as is his love for the majestic grizzly bears who inhabit them. He spent his spare time mountain climbing, fishing, skiing, snowshoeing, and hiking in the woods near his home. This book is an eclectic collection of stories about family, friends, and adventures, all sprinkled with the author’s unique sense of humour.</p>
    </div>
  </section>

  <section class="spine">
    <div class="spine-photo" role="img" aria-label="Two smiling hikers on a green alpine slope"></div>
    <div class="spine-title">Songs From The Old Trapline</div>
  </section>

  <section class="front-cover">
    <div class="front-photo" role="img" aria-label="A smiling couple in hiking jackets standing in an alpine meadow of wildflowers below a steep green mountainside"></div>

    <h1 class="title-block">
      <span class="title-line title-line--lead">Songs From <span class="title-small">The Old</span></span>
      <span class="title-line title-line--hero">Trapline</span>
    </h1>

    <svg class="photo-insets" viewBox="0 0 222 316">
      <defs>
        <linearGradient id="inset-hunter" x1="0" y1="0" x2="1" y2="1">
          <stop offset="0" stop-color="#6f7a3e"/>
          <stop offset="0.5" stop-color="#8a7350"/>
          <stop offset="1" stop-color="#5e6a30"/>
        </linearGradient>
        <linearGradient id="inset-bear" x1="0" y1="0" x2="0" y2="1">
          <stop offset="0" stop-color="#7a5a4a"/>
          <stop offset="0.5" stop-color="#a59a8c"/>
          <stop offset="1" stop-color="#6b7a4a"/>
        </linearGradient>
      </defs>
      <polygon points="40,0 222,0 186,74 222,158 0,158 40,76" fill="#ffffff"/>
      <polygon points="0,158 222,158 186,240 222,316 40,316 0,240" fill="#ffffff"/>
      <g role="img" aria-label="A hunter with a rifle and pack frame walking on a hillside">
        <polygon points="6,12 174,12 200,80 210,152 42,152 20,80" fill="url(#inset-hunter)"/>
      </g>
      <g role="img" aria-label="A grizzly bear crossing a patchy snowfield">
        <polygon points="6,165 210,165 188,240 170,304 20,304 22,240" fill="url(#inset-bear)"/>
      </g>
    </svg>

    <div class="author-band">
      <svg viewBox="0 0 326 83" preserveAspectRatio="none" aria-hidden="true">
        <polygon points="38,0 326,0 326,83 0,83" fill="var(--author-band)"/>
      </svg>
      <p class="author-name">Reginald Hugh Pettigrew</p>
      <div class="author-rule"></div>
      <p class="author-credit">As told to Wendy Falkner</p>
    </div>
  </section>

</div>
</body>
</html>
```